BRISKEL Need a luxury modern business card designed.

Need a luxury modern business card designed. refer to the uploaded files for the company name and logo in the zip file under source files. i will making my descion on monday. so please send in before then so if we need to edit we will have the time. we have a trade show coming up and im on a deadline for printer.

Target Market(s)

high end clients

Contact Information for Business Card

Company nAme and logo. Tobias Fennick Co-Founder / Project Manager Office # 555-318-7094 Cell # 555-642-1586 BRISKEL.CA Tobias@briskel-example.ca

Font styles to use
Other font styles liked:
• Modern

Requirements
Must have
• Company name and logo, contact info, using the black, gold and white color scheme.

```html
<!DOCTYPE html>
<html lang="en">
<head>
<meta charset="utf-8">
<title>BRISKEL Business Card</title>
<link href="https://fonts.googleapis.com/css2?family=Montserrat:wght@700&family=Work+Sans:wght@300;400&display=swap" rel="stylesheet">
<style>
  :root {
    --backdrop: #4a4a4a;
    --card-dark: #2f2f31;
    --card-light: #ffffff;
    --gold: #a39465;
    --ink: #2b2b2b;
    --ink-soft: #505050;
    --white: #ffffff;
  }
  * { margin: 0; padding: 0; box-sizing: border-box; }
  html, body {
    width: 1200px; height: 1125px; overflow: hidden;
    background: var(--backdrop);
    font-family: "Work Sans", Arial, sans-serif;
  }
  .canvas {
    position: relative; width: 1200px; height: 1125px;
    display: flex; flex-direction: column; align-items: center;
    justify-content: center; gap: 50px;
  }
  .card {
    position: relative; width: 820px; height: 468px;
    box-shadow: 0 10px 28px rgba(0,0,0,.35);
  }
  .card--front { background: var(--card-dark); }
  .card--back { background: var(--card-light); display: flex; align-items: center; }

  .brand {
    display: flex; align-items: center; gap: 16px;
    font-family: "Work Sans", Arial, sans-serif; font-weight: 300;
    letter-spacing: .18em; line-height: 1;
  }
  .brand__mark { width: 18px; height: 18px; background: var(--gold); }
  .card--front .brand {
    position: absolute; right: 70px; top: 190px;
    font-size: 50px; color: var(--white);
  }
  .card--back .brand {
    font-size: 52px; color: var(--ink);
    flex-direction: column; gap: 30px;
  }
  .card--back .brand__mark { width: 28px; height: 28px; }

  .back__logo { width: 420px; display: flex; justify-content: center; }
  .back__divider { width: 2px; height: 250px; background: var(--gold); }
  .back__details { padding-left: 40px; }

  .person__name {
    font-family: "Montserrat", Arial, sans-serif; font-weight: 700;
    font-size: 28px; letter-spacing: .05em; color: var(--gold);
    text-transform: uppercase;
  }
  .person__role {
    font-size: 22px; color: var(--ink-soft); letter-spacing: .04em;
    margin-top: 4px; margin-bottom: 34px;
  }
  .contact-list { list-style: none; }
  .contact-list li {
    display: flex; align-items: center; gap: 10px;
    font-size: 23px; color: var(--ink-soft); letter-spacing: .04em;
    line-height: 1.4;
  }
  .contact-list svg { width: 18px; height: 18px; fill: var(--gold); flex: none; }
</style>
</head>
<body>
<main class="canvas">
  <section class="card card--front" aria-label="Card front">
    <div class="brand"><span class="brand__mark"></span><span>BRISKEL</span></div>
  </section>

  <section class="card card--back" aria-label="Card back">
    <div class="back__logo">
      <div class="brand"><span class="brand__mark"></span><span>BRISKEL</span></div>
    </div>
    <div class="back__divider"></div>
    <div class="back__details">
      <h1 class="person__name">Tobias Fennick</h1>
      <p class="person__role">Co-Founder / Project Manager</p>
      <ul class="contact-list">
        <li>
          <svg viewBox="0 0 24 24" aria-hidden="true"><path d="M6.6 10.8a15 15 0 0 0 6.6 6.6l2.2-2.2a1 1 0 0 1 1-.25 11.4 11.4 0 0 0 3.6.57 1 1 0 0 1 1 1V20a1 1 0 0 1-1 1A17 17 0 0 1 3 4a1 1 0 0 1 1-1h3.5a1 1 0 0 1 1 1c0 1.25.2 2.45.57 3.57a1 1 0 0 1-.25 1z"/></svg>
          555-318-7094
        </li>
        <li>
          <svg viewBox="0 0 24 24" aria-hidden="true"><path d="M7 1h10a2 2 0 0 1 2 2v18a2 2 0 0 1-2 2H7a2 2 0 0 1-2-2V3a2 2 0 0 1 2-2zm0 3v14h10V4zm5 15.5a1 1 0 1 0 0 2 1 1 0 0 0 0-2z"/></svg>
          555-642-1586
        </li>
        <li>
          <svg viewBox="0 0 24 24" aria-hidden="true"><path d="M2 5h20v14H2zm2 2v.5l8 5 8-5V7zm0 2.8V17h16V9.8l-8 5z"/></svg>
          Tobias@briskel-example.ca
        </li>
        <li>
          <svg viewBox="0 0 24 24" aria-hidden="true"><circle cx="12" cy="12" r="10"/></svg>
          BRISKEL.CA
        </li>
      </ul>
    </div>
  </section>
</main>
</body>
</html>
```